BRISKLY sparkling water needs new artwork! Based in Southern California

"Briskly" is a new sparkling water company based in Southern California that offers refreshing flavors (lime, cherry, & mango) with B vitamins and antioxidants.

We would like to see packaging designs for standard 12oz cans for each of the three flavors.
Our initial preference is to have individual artwork for each flavor.

Attached are examples of competitors' designs.
Updates

We are extending the deadline for the Thanksgiving Holiday. Thank you all for your contributions.

```html
<!DOCTYPE html>
<html lang="en">
<head>
<meta charset="utf-8">
<title>Briskly Sparkling Water – Cherry Label Template</title>
<link href="https://fonts.googleapis.com/css2?family=Cabin:wght@400;700&family=Roboto+Condensed:wght@400&family=Arimo:wght@700&family=Oswald:wght@500;700&display=swap" rel="stylesheet">
<style>
  :root {
    --guide: #a58bc4;
    --label-pink: #f4637a;
    --panel-blue: #4660c6;
    --ink: #1d1d1d;
    --white: #ffffff;
    --fruit-red: #e0182c;
  }
  * { margin: 0; padding: 0; box-sizing: border-box; }
  html, body { width: 1200px; height: 714px; overflow: hidden; background: var(--white); }
  .template { position: relative; width: 1200px; height: 714px; font-family: "Cabin", sans-serif; }
  .guides { position: absolute; inset: 0; }
  .abs { position: absolute; }
  .template-title { left: 0; width: 1204px; top: 8px; text-align: center; font-size: 27px; font-weight: 400; color: var(--guide); }
  .note { font-size: 11px; color: var(--guide); white-space: nowrap; }
  .note-center { transform: translateX(-50%); }
  .note-small { font-size: 8.5px; text-align: center; line-height: 11px; }
  .transition-title { font-family: "Arimo", sans-serif; font-weight: 700; font-size: 13px; color: var(--guide); }
  .transition-sub { font-family: "Roboto Condensed", sans-serif; font-size: 9.5px; color: var(--guide); }
  .cut-height { font-size: 12.5px; color: var(--guide); line-height: 16px; }
  .slit-width { font-family: "Roboto Condensed", sans-serif; font-size: 13px; color: var(--guide); text-align: center; line-height: 15px; transform: translateX(-50%); }

  .brand-name { font-family: "Cabin", sans-serif; font-weight: 700; color: var(--ink); text-align: center; letter-spacing: -0.5px; line-height: 1; }
  .brand-side { left: 205px; top: 212px; width: 136px; font-size: 38px; }
  .brand-front { left: 492px; top: 214px; width: 200px; font-size: 52px; }

  .story-panel { left: 187px; top: 265px; width: 183px; height: 316px; background: var(--panel-blue); color: var(--white);
    font-size: 12px; line-height: 16px; text-align: center; padding-top: 6px; white-space: nowrap; letter-spacing: -0.1px; }
  .story-divider { display: block; width: 126px; height: 3px; background: var(--white); margin: 15px auto 20px; }

  .flavor-art { left: 395px; top: 272px; width: 388px; height: 324px; border-radius: 46% 46% 40% 40%;
    background: radial-gradient(ellipse at 50% 45%, #f7a0ac 0%, #f07e8d 45%, var(--label-pink) 75%); }
  .copy { font-family: "Oswald", sans-serif; text-align: center; text-transform: uppercase; line-height: 1; }
  .product-cloud { left: 488px; top: 311px; width: 206px; height: 134px; background: var(--white);
    border: 3px solid var(--ink); border-radius: 70px 70px 40px 40px; padding-top: 16px; color: var(--ink); font-weight: 700; }
  .product-cloud .line-1 { font-size: 40px; letter-spacing: 1px; }
  .product-cloud .line-2 { font-size: 56px; letter-spacing: 2px; margin-top: -2px; }
  .claim-banner { left: 508px; top: 442px; width: 161px; height: 32px; background: var(--panel-blue); border: 2px solid var(--ink); padding-top: 2px; }
  .claim-banner .claim-main { color: var(--fruit-red); font-size: 15px; font-weight: 700; letter-spacing: 0.5px; }
  .claim-banner .claim-sub { color: var(--white); font-size: 9px; font-weight: 500; margin-top: 1px; }
  .flavor-badge { left: 579px; top: 486px; width: 125px; height: 82px; background: var(--panel-blue); border: 2px solid var(--ink);
    border-radius: 44px 40px 46px 12px; color: var(--white); font-weight: 500; padding-top: 8px; }
  .flavor-badge .flavor-name { font-size: 31px; letter-spacing: 1px; }
  .flavor-badge .flavor-word { font-size: 23px; letter-spacing: 1px; margin-top: 2px; }
  .volume { left: 603px; top: 576px; width: 78px; color: var(--white); font-size: 12px; font-weight: 500; }

  .info-box { background: var(--white); color: #000; font-size: 12.5px; display: flex; align-items: center; justify-content: center; }
  .nutrition-box { left: 803px; top: 231px; width: 162px; height: 242px; }
  .barcode-box { left: 803px; top: 504px; width: 162px; height: 63px; }
</style>
</head>
<body>
<main class="template">
  <svg class="guides" width="1200" height="714" viewBox="0 0 1200 714" aria-hidden="true">
    <defs>
      <marker id="arrow-head" viewBox="0 0 10 10" refX="9" refY="5" markerWidth="6" markerHeight="6" orient="auto-start-reverse">
        <path d="M0 0 L10 5 L0 10 z" fill="#a58bc4"/>
      </marker>
    </defs>
    <rect x="382" y="102.5" width="412" height="518" fill="none" stroke="#a58bc4" stroke-width="1"/>
    <rect x="163" y="141" width="830" height="468" fill="#f4637a"/>
    <rect x="163" y="141" width="849" height="468" fill="none" stroke="#a58bc4" stroke-width="1"/>
    <rect x="167" y="149" width="827" height="452" fill="none" stroke="#c8a0d8" stroke-width="0.8"/>
    <line x1="382" y1="141" x2="382" y2="609" stroke="#c8a0d8" stroke-width="0.8"/>
    <line x1="794" y1="141" x2="794" y2="609" stroke="#c8a0d8" stroke-width="0.8"/>
    <line x1="138" y1="195" x2="1038" y2="195" stroke="#a58bc4" stroke-width="1" stroke-dasharray="8 6"/>
    <g stroke="#a58bc4" stroke-width="0.8">
      <line x1="163" y1="82" x2="163" y2="130"/><line x1="167" y1="82" x2="167" y2="130"/>
      <line x1="993" y1="82" x2="993" y2="130"/><line x1="1012" y1="82" x2="1012" y2="130"/>
      <line x1="89" y1="141" x2="137" y2="141"/><line x1="89" y1="149" x2="137" y2="149"/>
      <line x1="1027" y1="141" x2="1075" y2="141"/><line x1="1027" y1="149" x2="1075" y2="149"/>
      <line x1="91" y1="601" x2="139" y2="601"/><line x1="91" y1="609" x2="139" y2="609"/>
      <line x1="1032" y1="601" x2="1080" y2="601"/><line x1="1032" y1="609" x2="1080" y2="609"/>
      <line x1="167" y1="620" x2="167" y2="654"/><line x1="1012" y1="620" x2="1012" y2="658"/>
    </g>
    <g stroke="#a58bc4" stroke-width="0.8" stroke-dasharray="2 3">
      <line x1="170" y1="102" x2="170" y2="652"/>
      <line x1="990" y1="126" x2="990" y2="638"/>
    </g>
    <line x1="168" y1="636" x2="517" y2="636" stroke="#a58bc4" stroke-width="1" marker-start="url(#arrow-head)"/>
    <line x1="646" y1="636" x2="1010" y2="636" stroke="#a58bc4" stroke-width="1" marker-end="url(#arrow-head)"/>
    <circle cx="1047" cy="94" r="3" fill="#a58bc4"/>
    <line x1="1047" y1="94" x2="1006" y2="144" stroke="#a58bc4" stroke-width="1.2" marker-end="url(#arrow-head)"/>
  </svg>

  <h1 class="abs template-title">109 mm LF_4.875”_Template</h1>
  <div class="abs note" style="left:143px;top:61px">1 mm clear</div>
  <div class="abs note" style="left:973px;top:61px">5 mm clear</div>
  <div class="abs note note-center" style="left:598px;top:80px">109 mm LF</div>
  <div class="abs transition-title" style="left:1037px;top:61px">Transitional Area</div>
  <div class="abs transition-sub" style="left:1037px;top:76px">(transitions from sidewall to neck)</div>
  <div class="abs note" style="left:24px;top:140px">2 mm clear</div>
  <div class="abs note" style="left:1082px;top:140px">2 mm clear</div>
  <div class="abs note" style="left:25px;top:598px">2 mm clear</div>
  <div class="abs note" style="left:1087px;top:598px">2 mm clear</div>
  <div class="abs cut-height" style="left:1032px;top:346px">4.875” Cut Height<br>123.825 MM</div>
  <div class="abs slit-width" style="left:579px;top:628px">225 MM SLIT WIDTH<br>8.8583”</div>
  <div class="abs note note-small" style="left:160px;top:671px;width:70px">1mm Bkgd Bleed<br>Overlap</div>
  <div class="abs note note-small" style="left:895px;top:654px;width:80px">2mm Bkgd Only<br>No Text/Art</div>

  <div class="abs brand-name brand-side">Briskly</div>
  <section class="abs story-panel">
    <p>Lorem Ipsum is simply dummy<br>text of the printing and<br>typesetting industry. Lorem<br>Ipsum has been the industry's<br>standard dummy text ever<br>since the 1500s, when an</p>
    <span class="story-divider"></span>
    <p>unknown printer took a galley<br>of type and scrambled it to<br>make a type specimen book. It<br>has survived not only five<br>centuries, but also the leap into<br>electronic typesetting, remai-<br>ning essentially unchanged. It<br>was popularised in the 1960s<br>with the release of Letraset<br>sheets containing Lorem Ipsum<br>passages, and</p>
  </section>

  <div class="abs brand-name brand-front">Briskly</div>
  <div class="abs flavor-art" role="img" aria-label="Hand-drawn cherry artwork: waves, bubbles, leaves and cherries around the product name"></div>
  <div class="abs copy product-cloud">
    <div class="line-1">Sparkling</div>
    <div class="line-2">Water</div>
  </div>
  <div class="abs copy claim-banner">
    <div class="claim-main">With Real Fruit</div>
    <div class="claim-sub">And B Vitamins</div>
  </div>
  <div class="abs copy flavor-badge">
    <div class="flavor-name">Cherry</div>
    <div class="flavor-word">Flavor</div>
  </div>
  <div class="abs copy volume">12oz (355ml)</div>

  <div class="abs info-box nutrition-box">Nutrition box</div>
  <div class="abs info-box barcode-box">Barcode</div>
</main>
</body>
</html>
```